Web design for Crowdfunding site HopeWingsRally.com

We need a web design for christian crowdfunding website. Here is the challenge: We need responsive layout that is targeted first in iPad size of screen. It should also scale somehow down to iPhone size of screens. Web layout can be about the same size as iPad screen.

Screens should work so that main page scrolls not but only certain part of the screen scrolls and always one "page" at time. We can implement these "scrolls" then later with javascript but now we need only design. The challenge is to create this kind of hybrid website / app look.

Target is at first to raise funds to orphan people needing about $40 per month for their living and education. There is always some organization which takes care of these kids. Later there will be other christian missions included. At first we are looking to find monthly supporters.

You can be as creative as you want :) As you see from the look and feel sector, I am not looking any same traditional look which many "help kids" sites have. I am looking to reach now younger generation and therefore iPad and mobile are the main screen sizes.

Inspirational designs:
- https://example-gallery.test/profiles/studiofernlake/designs/482716?from=%2Fbrowse%2Fxhr%2Fdesigns%3Fcategory%3Dmobile-app-design
- http://www.artpoolhub.test/design/8261047 Clear, simple visuals
- http://www.artpoolhub.test/design/7394215 Header
- http://www.artpoolhub.test/design/6048392 Contrast in the colors, i think is powerfull

Some terms could be: Kids play, kids are learning (in the school). No static posture but living like kids are. I wonder also how we could also add little bit gaming style even though the question is of reali life of real people. Giving should be rewarding.

Target Market(s)

People who want help other people.

Industry/Entity Type

Christian

Number of Pages Required

4 page

Requirements
Must have
• Homepage. Mission page (In my wireframes it was one kid).
Nice to have
• Other pages and some idea how to scroll. 4 pages is no must. If you feel easy, please give first some draft and I give comments on that.

```html
<!DOCTYPE html>
<html lang="en">
<head>
<meta charset="utf-8">
<title>HopeWingsRally – Christian Crowd Funding</title>
<link rel="stylesheet" href="https://fonts.googleapis.com/css2?family=Roboto:ital,wght@0,400;0,500;0,700;1,500&family=Open+Sans:wght@400;600&display=swap">
<style>
  :root {
    --black: #000000;
    --ink: #111010;
    --yellow: #ffc000;
    --white: #ffffff;
    --grey-dash: #8a8a8a;
    --ring: #c9c9c9;
    --burlap-dark: #1c1918;
    --burlap-mid: #3a3432;
    --icon-grey: #9a9a9a;
  }
  * { box-sizing: border-box; margin: 0; padding: 0; }
  html, body {
    width: 1200px; height: 652px; overflow: hidden;
    background: var(--black);
    font-family: "Roboto", Arial, sans-serif;
    color: var(--white);
  }
  .page { position: relative; width: 1200px; height: 652px; overflow: hidden; }

  /* Header */
  .site-header {
    position: absolute; inset: 0 0 auto 0; height: 82px;
    background: var(--black);
    border-top: 3px solid var(--yellow);
    z-index: 2;
  }
  .nav-left { position: absolute; left: 126px; top: 30px; display: flex; align-items: center; }
  .menu-icon { width: 22px; height: 20px; margin-right: 26px; }
  .nav-link {
    font-size: 13px; font-weight: 500; letter-spacing: .2px;
    text-transform: uppercase; color: var(--white); text-decoration: none;
  }
  .search-icon { width: 20px; height: 20px; margin-left: 28px; }
  .brand {
    position: absolute; left: 0; right: 0; top: 22px; text-align: center;
    font-size: 29px; font-weight: 500; color: var(--yellow); letter-spacing: -.3px;
  }
  .nav-right { position: absolute; right: 127px; top: 32px; display: flex; gap: 40px; }
  .nav-right .nav-link { display: flex; align-items: center; gap: 6px; }
  .nav-right svg { width: 12px; height: 12px; }

  /* Hero */
  .hero-backdrop {
    position: absolute; left: 0; top: 82px; width: 1200px; height: 570px;
    background:
      radial-gradient(ellipse 420px 300px at 300px 200px, rgba(80,62,50,.55), transparent 70%),
      radial-gradient(ellipse 900px 500px at 600px 250px, var(--burlap-mid), var(--burlap-dark) 80%);
  }
  .hero-copy { position: absolute; left: 125px; top: 228px; width: 470px; }
  .hero-title { font-size: 41px; font-weight: 700; line-height: 1.1; letter-spacing: .2px; }
  .hero-lede { margin-top: 16px; font-size: 16px; font-weight: 500; line-height: 35px; }
  .pledge-band {
    position: absolute; left: 126px; top: 376px; width: 360px; height: 58px;
    background: linear-gradient(90deg, var(--yellow) 0%, var(--yellow) 60%, rgba(255,192,0,0) 100%);
    color: var(--ink); display: flex; align-items: center; padding-left: 20px;
  }
  .pledge-amount { font-size: 17px; font-weight: 700; margin-right: 8px; }
  .pledge-note { font-size: 16px; font-weight: 500; font-style: italic; }

  .mission-ring { position: absolute; left: 650px; top: 130px; width: 440px; height: 420px; }
  .ring-label { font-family: "Roboto", Arial, sans-serif; font-weight: 500; font-size: 28px; fill: var(--white); }

  /* Footer */
  .site-footer {
    position: absolute; left: 126px; right: 126px; top: 606px;
    display: flex; justify-content: space-between; align-items: center;
    font-family: "Open Sans", Arial, sans-serif; font-size: 11px; color: var(--white);
  }
  .copyright .brand-mention { color: var(--yellow); }
  .follow { display: flex; align-items: center; gap: 22px; }
  .social-dot { width: 9px; height: 9px; border-radius: 50%; background: var(--icon-grey); }
  .social-dot.is-active { background: var(--yellow); }
</style>
</head>
<body>
<div class="page">
  <header class="site-header">
    <nav class="nav-left">
      <svg class="menu-icon" viewBox="0 0 22 20" aria-hidden="true">
        <rect x="0" y="1" width="4" height="4" rx="1" fill="#fff"/>
        <rect x="6" y="1" width="16" height="4" rx="1" fill="#fff"/>
        <rect x="0" y="8" width="4" height="4" rx="1" fill="#fff"/>
        <rect x="6" y="8" width="16" height="4" rx="1" fill="#fff"/>
        <rect x="0" y="15" width="4" height="4" rx="1" fill="#fff"/>
        <rect x="6" y="15" width="16" height="4" rx="1" fill="#fff"/>
      </svg>
      <a class="nav-link" href="#">See the missions</a>
      <svg class="search-icon" viewBox="0 0 20 20" aria-hidden="true">
        <circle cx="8" cy="8" r="6.5" fill="none" stroke="#fff" stroke-width="1.6"/>
        <line x1="12.8" y1="12.8" x2="19" y2="19" stroke="#fff" stroke-width="1.8"/>
      </svg>
    </nav>
    <div class="brand">HopeWingsRally</div>
    <nav class="nav-right">
      <a class="nav-link" href="#">
        <svg viewBox="0 0 12 12" aria-hidden="true"><rect x="1.5" y="5" width="9" height="7" rx="1" fill="#fff"/><path d="M3.5 5V3.5a2.5 2.5 0 0 1 5 0V5" fill="none" stroke="#fff" stroke-width="1.5"/></svg>
        Log in
      </a>
      <a class="nav-link" href="#">
        <svg viewBox="0 0 12 12" aria-hidden="true"><path d="M0 4.5h5V2l4 4-4 4V7.5H0z" fill="#fff"/><path d="M7 1h4v10H7" fill="none" stroke="#fff" stroke-width="1.4"/></svg>
        Sign up
      </a>
    </nav>
  </header>

  <main>
    <div class="hero-backdrop" role="img" aria-label="Dark burlap texture with a wooden cross lying on it"></div>

    <section class="hero-copy">
      <h1 class="hero-title">Christian Crowd Funding</h1>
      <p class="hero-lede">She has a name.He has dreams.She hopes she would have a future.He is like you.</p>
    </section>

    <div class="pledge-band">
      <span class="pledge-amount">1 USD</span>
      <span class="pledge-note">a month will help her and him</span>
    </div>

    <svg class="mission-ring" viewBox="0 0 440 420" aria-label="Children supported by the missions">
      <defs>
        <linearGradient id="photo-blue" x1="0" y1="0" x2="0" y2="1"><stop offset="0" stop-color="#6fa6c9"/><stop offset="1" stop-color="#3fb8b0"/></linearGradient>
        <linearGradient id="photo-wood" x1="0" y1="0" x2="0" y2="1"><stop offset="0" stop-color="#9a8a4a"/><stop offset="1" stop-color="#6b4a32"/></linearGradient>
        <linearGradient id="photo-family" x1="0" y1="0" x2="0" y2="1"><stop offset="0" stop-color="#b7a58e"/><stop offset="1" stop-color="#d97a8a"/></linearGradient>
        <linearGradient id="photo-orange" x1="0" y1="0" x2="0" y2="1"><stop offset="0" stop-color="#c9b8a8"/><stop offset="1" stop-color="#f29a38"/></linearGradient>
      </defs>
      <!-- ring path: centre 218,207 radius 143 -->
      <path d="M218 64 A143 143 0 0 0 218 350" fill="none" stroke="var(--yellow)" stroke-width="4" stroke-dasharray="10 7"/>
      <path d="M218 64 A143 143 0 0 1 218 350" fill="none" stroke="var(--grey-dash)" stroke-width="4" stroke-dasharray="10 7"/>

      <text class="ring-label" x="218" y="206" text-anchor="middle">HopeWings</text>
      <text class="ring-label" x="218" y="248" text-anchor="middle">Rally</text>

      <g role="img" aria-label="Photo of a young girl in a teal shirt">
        <circle cx="218" cy="67" r="59" fill="url(#photo-blue)" stroke="var(--ring)" stroke-width="4"/>
      </g>
      <g role="img" aria-label="Photo of a thoughtful boy leaning on a wooden fence">
        <circle cx="73" cy="211" r="59" fill="url(#photo-wood)" stroke="var(--yellow)" stroke-width="4"/>
      </g>
      <g role="img" aria-label="Photo of a smiling woman with two small girls">
        <circle cx="362" cy="211" r="59" fill="url(#photo-family)" stroke="var(--ring)" stroke-width="4"/>
      </g>
      <g role="img" aria-label="Photo of a little girl in an orange shirt">
        <circle cx="218" cy="347" r="59" fill="url(#photo-orange)" stroke="var(--ring)" stroke-width="4"/>
      </g>
    </svg>
  </main>

  <footer class="site-footer">
    <p class="copyright">COPYRIGHTS © 2016 . <span class="brand-mention">HOPEWINGSRALLY</span> | ALLRIGHTS RESERVED.</p>
    <div class="follow">
      <span>FOLLOW US :</span>
      <span class="social-dot is-active" aria-label="Social network 1"></span>
      <span class="social-dot" aria-label="Social network 2"></span>
      <span class="social-dot" aria-label="Social network 3"></span>
      <span class="social-dot" aria-label="Social network 4"></span>
      <span class="social-dot" aria-label="Social network 5"></span>
    </div>
  </footer>
</div>
</body>
</html>
```